Business Card & Email Signature Design || Upmarket + Luxury

Rima Vale Honey, a New Zealand Manuka Honey company needs a Business Card & Email Signature design.

Our logo's are attached in Gold & Black versions, feel free to be creative with how you use the logo and it's patterns in your design.

Style:
- Looking for an Elegant, Luxurious, Upmarket feel.
- Black/Matte Black Card, Gold Foil, UV Embossing

Information to Add:

- Logo
- Company Name: Rima Vale Honey
- Name: Martin Holloway
- Title: Creative Director
- Phone: +64 2815 96 417
- Email: martin@rimavalehoney.example.nz
- Website: www.rimavalehoney.example.nz

- Socials: ***For email Signature Only***
- Facebook: https://www.facebook.com/rimavalehoney/
- Instagram: https://www.instagram.com/rimavalehoney/

Target Market(s)

Asia/Europe Luxury, Upmarket

Contact Information for Business Card

- Logo
- Name: Martin Holloway
- Phone: +64 2815 96 417

Font styles to use
Other font styles liked:
• Champagne & Limousines (Attached)

Requirements
Must have
• Business Card & Email Signature Design.

Looking for a Sleek, Luxury, Upmarket Design.

```html
<!DOCTYPE html>
<html lang="en">
<head>
<meta charset="utf-8">
<title>Rima Vale Honey — Business Card</title>
<link rel="stylesheet" href="https://fonts.googleapis.com/css2?family=Montserrat:wght@300;400;500&display=swap">
<style>
  :root {
    --backdrop: #2a2a2c;
    --card: #161617;
    --card-edge: #0e0e0f;
    --emboss-light: #232325;
    --emboss-dark: #121213;
    --gold: #c9a85a;
    --gold-soft: #a88d4e;
  }
  * { box-sizing: border-box; margin: 0; padding: 0; }
  html, body { width: 1200px; height: 1017px; overflow: hidden; }
  body {
    background: radial-gradient(ellipse at 50% 40%, #353537 0%, var(--backdrop) 70%);
    font-family: "Montserrat", sans-serif;
    position: relative;
  }
  .card {
    position: absolute;
    left: 220px;
    width: 760px;
    height: 434px;
    background: var(--card);
    border-radius: 4px;
    box-shadow: 0 18px 40px rgba(0,0,0,.55), 0 0 0 1px var(--card-edge);
    overflow: hidden;
  }
  .card--front { top: 60px; }
  .card--back { top: 530px; }

  .emboss-motif {
    position: absolute;
    border-radius: 48% 52% 40% 60% / 55% 45% 55% 45%;
    background: radial-gradient(circle at 40% 40%, var(--emboss-light), var(--emboss-dark) 75%);
    opacity: .9;
  }
  .card--front .emboss-motif { left: 70px; top: 110px; width: 330px; height: 250px; }
  .card--back .emboss-motif { left: 400px; top: 30px; width: 310px; height: 240px; }

  .brand-seal {
    position: absolute;
    right: 70px;
    top: 48px;
    width: 200px;
    height: 200px;
    border: 2px solid var(--gold);
    border-radius: 50%;
    display: flex;
    align-items: center;
    justify-content: center;
    text-align: center;
  }
  .brand-seal__name {
    color: var(--gold);
    font-weight: 400;
    font-size: 17px;
    letter-spacing: 3px;
    line-height: 1.5;
    text-transform: uppercase;
  }

  .contact {
    position: absolute;
    left: 60px;
    bottom: 60px;
    color: var(--gold);
  }
  .contact__name {
    font-weight: 500;
    font-size: 26px;
    letter-spacing: 2px;
    text-transform: uppercase;
  }
  .contact__title {
    font-weight: 300;
    font-size: 17px;
    color: var(--gold-soft);
    margin-top: 4px;
  }
  .contact__rule {
    width: 60px;
    height: 2px;
    background: var(--gold);
    margin: 20px 0 16px;
  }
  .contact__list { list-style: none; }
  .contact__item {
    display: flex;
    align-items: center;
    gap: 12px;
    font-weight: 300;
    font-size: 17px;
    line-height: 32px;
  }
  .contact__icon { width: 16px; height: 16px; flex: none; }
</style>
</head>
<body>

<section class="card card--front" aria-label="Card front">
  <div class="emboss-motif" role="img" aria-label="Blind-embossed decorative bee pattern"></div>
  <div class="brand-seal">
    <span class="brand-seal__name">Rima Vale<br>Honey</span>
  </div>
</section>

<section class="card card--back" aria-label="Card back">
  <div class="emboss-motif" role="img" aria-label="Blind-embossed decorative bee pattern"></div>
  <div class="contact">
    <h1 class="contact__name">Martin Holloway</h1>
    <p class="contact__title">Creative Director</p>
    <div class="contact__rule"></div>
    <ul class="contact__list">
      <li class="contact__item">
        <svg class="contact__icon" viewBox="0 0 16 16" aria-hidden="true"><path d="M4 1.5l2.2 2.8-1.4 1.6c.9 2 2.6 3.7 4.6 4.6l1.6-1.4 2.8 2.2-1.3 2.2C7 13.5 2.5 9 2 3z" fill="var(--gold)"/></svg>
        +64 2815 96 417
      </li>
      <li class="contact__item">
        <svg class="contact__icon" viewBox="0 0 16 16" aria-hidden="true"><rect x="1" y="3" width="14" height="10" fill="var(--gold)"/><path d="M1.5 3.5L8 9l6.5-5.5" stroke="var(--card)" stroke-width="1.3" fill="none"/></svg>
        martin@rimavalehoney.example.nz
      </li>
      <li class="contact__item">
        <svg class="contact__icon" viewBox="0 0 16 16" aria-hidden="true"><circle cx="8" cy="8" r="7" fill="var(--gold)"/><path d="M1 8h14M8 1c-3 3.5-3 10.5 0 14M8 1c3 3.5 3 10.5 0 14" stroke="var(--card)" stroke-width="1" fill="none"/></svg>
        www.rimavalehoney.example.nz
      </li>
    </ul>
  </div>
</section>

</body>
</html>
```